FinTech company looking to revamp and expand client-facing interface for our financial models

Pellworth Engines currently has a very simple website that allows clients to interact with our financial models. We are looking to completely redesign the current site and add several extra pages to provide extra functionality. We want the design to have a modern, slick feel, that will work on both a desktop or a tablet. It should be straightforward for clients to move between different pages at any time, and clear from the layout how to interact with the more advanced features. We have included screenshots of existing pages in the attached design brief, as well as sketches of the functionality required by the new pages, but can't provide a direct link to the current site.
Target Market(s)
Professional investors that will be paying to access the interface
Industry/Entity Type
Finance
Number of Pages Required
4 page
Colors
Designer to choose colors to be used in the design.
Look and feel
Each slider illustrates characteristics of the customer's brand and the style your logo design should communicate.

```html
<!DOCTYPE html>
<html lang="en">
<head>
<meta charset="utf-8">
<title>Pellworth Engines – Backtest</title>
<link href="https://fonts.googleapis.com/css2?family=Open+Sans:wght@400;600;700&family=Roboto+Condensed:wght@400&display=swap" rel="stylesheet">
<style>
:root{
  --navy:#0b2f5e;
  --ink:#1a1a1a;
  --frame:#e4e4e4;
  --page:#ebebeb;
  --white:#ffffff;
  --line:#dddddd;
  --row-alt:#efefef;
  --olive:#b8b73b;
  --blue:#3b6aa8;
  --muted:#666666;
}
*{box-sizing:border-box;margin:0;padding:0}
html,body{width:1200px;height:1122px;overflow:hidden;background:var(--frame)}
.stage{width:1300px;height:1215px;transform:scale(0.923077);transform-origin:0 0;position:relative;font-family:"Open Sans",sans-serif;color:var(--ink)}
.app{position:absolute;left:15px;top:15px;width:1270px;height:1185px;background:linear-gradient(#dcdcdc 0,var(--page) 40px,#f1f1f1 100%)}
.topbar{position:absolute;left:0;top:0;width:1270px;height:60px;background:var(--white);display:flex}
.topbar .cell{height:60px;display:flex;align-items:center;justify-content:center;border-right:1px solid var(--line);font-weight:700;font-size:14px;gap:8px}
.brand{width:180px;font-size:18px}
.horizon{width:90px}
.spacer{width:135px}
.nav-models{width:140px}
.nav-sens{width:178px}
.nav-port{width:160px}
.nav-back{width:152px;background:var(--navy);color:var(--white);border-right:none}
.chart-card{position:absolute;left:90px;top:100px;width:1160px;height:425px;background:var(--white);box-shadow:0 2px 6px rgba(0,0,0,.15)}
.tabstrip{height:85px;background:#efefef;position:relative}
.tab{position:absolute;bottom:0;height:35px;display:flex;align-items:center;justify-content:center;font-size:13px;font-weight:600;background:var(--white);color:var(--muted)}
.tab.chart{left:55px;width:155px;background:var(--navy);color:var(--white)}
.tab.active{height:45px;background:var(--ink);color:var(--white);padding-bottom:8px}
.plot{position:absolute;left:0;top:85px}
.side-tab{position:absolute;left:0;top:472px;width:50px;height:250px;background:#2b2b2b;border-radius:0 4px 4px 0}
.side-tab span{position:absolute;left:12px;top:206px;transform:rotate(-90deg);transform-origin:0 0;color:var(--white);font-size:17px;font-weight:600;letter-spacing:.5px;white-space:nowrap}
.side-toggle{position:absolute;left:36px;top:583px}
.export{position:absolute;top:578px;display:flex;align-items:center;gap:6px;color:var(--navy);font-weight:700;font-size:17px}
.table{position:absolute;top:615px;background:var(--white);box-shadow:0 2px 6px rgba(0,0,0,.15);border-radius:4px;overflow:hidden}
.table .head{display:flex;height:70px;background:var(--ink);color:var(--white);font-weight:600;font-size:17px}
.table .head div{display:flex;align-items:center;justify-content:center;border-right:1px solid #3a3a3a}
.table .row{display:flex;height:69px;font-family:"Roboto Condensed",sans-serif;font-size:18px}
.table .row:nth-child(even){background:var(--row-alt)}
.table .row div{display:flex;align-items:center;justify-content:center;border-right:1px solid var(--line)}
.table .body{position:relative}
.scroll{position:absolute;top:0;right:0;width:40px;height:420px;background:#cfcfcf}
.scroll::before{content:"";position:absolute;left:12px;top:25px;width:18px;height:370px;border-radius:9px;background:var(--white);border:1px solid #bbb}
.scroll::after{content:"";position:absolute;left:11px;top:26px;width:20px;height:74px;border-radius:10px;background:#6d6d6d}
.stats{left:90px;width:400px}
.trades{left:530px;width:720px}
.col180{width:180px}
</style>
</head>
<body>
<div class="stage">
<div class="app">
  <header class="topbar">
    <div class="cell brand">PELLWORTH</div>
    <div class="cell horizon">250D</div>
    <div class="cell horizon">83D</div>
    <div class="cell horizon">42D</div>
    <div class="cell spacer"></div>
    <div class="cell nav-models">
      <svg width="24" height="22" viewBox="0 0 24 22"><path d="M2 11 12 2l10 9M5 9v11h5v-6h4v6h5V9" fill="none" stroke="#1a1a1a" stroke-width="2.4"/></svg>MODELS</div>
    <div class="cell nav-sens">
      <svg width="24" height="24" viewBox="0 0 24 24" fill="#1a1a1a"><circle cx="12" cy="12" r="2"/><circle cx="12" cy="4" r="1.6"/><circle cx="12" cy="20" r="1.6"/><circle cx="4" cy="12" r="1.6"/><circle cx="20" cy="12" r="1.6"/><circle cx="6.5" cy="6.5" r="1.6"/><circle cx="17.5" cy="6.5" r="1.6"/><circle cx="6.5" cy="17.5" r="1.6"/><circle cx="17.5" cy="17.5" r="1.6"/><circle cx="12" cy="8" r="1.2"/><circle cx="12" cy="16" r="1.2"/><circle cx="8" cy="12" r="1.2"/><circle cx="16" cy="12" r="1.2"/></svg>SENSITIVITIES</div>
    <div class="cell nav-port">
      <svg width="24" height="24" viewBox="0 0 24 24" fill="none" stroke="#1a1a1a" stroke-width="2"><circle cx="6" cy="6" r="4"/><circle cx="18" cy="6" r="4"/><circle cx="6" cy="18" r="4"/><circle cx="18" cy="18" r="4"/></svg>PORTFOLIO</div>
    <div class="cell nav-back">
      <svg width="26" height="22" viewBox="0 0 26 22" fill="none" stroke="#fff" stroke-width="2"><rect x="2" y="2" width="22" height="18"/><path d="M6 16l5-6 4 3 6-7"/></svg>BACKTEST</div>
  </header>

  <section class="chart-card">
    <div class="tabstrip">
      <div class="tab chart">CHART</div>
      <div class="tab" style="left:215px;width:90px">#1</div>
      <div class="tab" style="left:310px;width:90px">#2</div>
      <div class="tab" style="left:405px;width:90px;height:40px">#3</div>
      <div class="tab active" style="left:500px;width:90px">#4</div>
    </div>
    <svg class="plot" width="1160" height="340" viewBox="90 185 1160 340" font-family="Open Sans, sans-serif" font-size="12" fill="#555">
      <g stroke="#eeeeee" stroke-width="1">
        <line x1="190" y1="263" x2="1110" y2="263"/><line x1="190" y1="300" x2="1110" y2="300"/>
        <line x1="190" y1="338" x2="1110" y2="338"/><line x1="190" y1="375" x2="1110" y2="375"/>
        <line x1="190" y1="413" x2="1110" y2="413"/>
        <line x1="217" y1="250" x2="217" y2="450"/><line x1="360" y1="250" x2="360" y2="450"/>
        <line x1="500" y1="250" x2="500" y2="450"/><line x1="641" y1="250" x2="641" y2="450"/>
        <line x1="777" y1="250" x2="777" y2="450"/><line x1="917" y1="250" x2="917" y2="450"/>
        <line x1="1058" y1="250" x2="1058" y2="450"/>
      </g>
      <line x1="190" y1="450" x2="1110" y2="450" stroke="#777"/>
      <g text-anchor="end"><text x="186" y="267">100</text><text x="186" y="304">80</text><text x="186" y="342">60</text><text x="186" y="379">40</text><text x="186" y="417">20</text><text x="186" y="454">0</text></g>
      <g text-anchor="middle"><text x="217" y="476">Jul 2018</text><text x="360" y="476">Sep 2018</text><text x="500" y="476">Nov 2018</text><text x="641" y="476">Jan 2019</text><text x="777" y="476">Mar 2019</text><text x="917" y="476">May 2019</text><text x="1058" y="476">Jul 2019</text></g>

      <g stroke-linecap="round" stroke-width="7" stroke-dasharray="0 6" fill="none">
        <path d="M237 263H322M322 266H370" stroke="var(--olive)"/>
        <path d="M795 266H1045" stroke="var(--olive)"/>
        <path d="M618 263H1062" stroke="var(--blue)"/>
      </g>
      <g fill="var(--olive)">
        <circle cx="325" cy="274" r="3.5"/><circle cx="333" cy="279" r="3.5"/><circle cx="350" cy="270" r="3.5"/><circle cx="368" cy="274" r="3.5"/>
        <circle cx="372" cy="330" r="3.5"/><circle cx="375" cy="360" r="3.5"/><circle cx="380" cy="380" r="3.5"/><circle cx="385" cy="342" r="3.5"/><circle cx="388" cy="367" r="3.5"/><circle cx="392" cy="372" r="3.5"/><circle cx="398" cy="378" r="3.5"/><circle cx="400" cy="360" r="3.5"/><circle cx="405" cy="356" r="3.5"/><circle cx="410" cy="368" r="3.5"/><circle cx="415" cy="322" r="3.5"/><circle cx="418" cy="327" r="3.5"/><circle cx="422" cy="302" r="3.5"/><circle cx="428" cy="290" r="3.5"/><circle cx="432" cy="293" r="3.5"/><circle cx="435" cy="265" r="3.5"/><circle cx="440" cy="270" r="3.5"/><circle cx="445" cy="267" r="3.5"/><circle cx="448" cy="325" r="3.5"/><circle cx="452" cy="336" r="3.5"/><circle cx="455" cy="350" r="3.5"/><circle cx="462" cy="344" r="3.5"/><circle cx="465" cy="355" r="3.5"/><circle cx="470" cy="395" r="3.5"/><circle cx="478" cy="418" r="3.5"/><circle cx="482" cy="405" r="3.5"/><circle cx="485" cy="398" r="3.5"/><circle cx="490" cy="410" r="3.5"/><circle cx="495" cy="420" r="3.5"/><circle cx="500" cy="440" r="3.5"/><circle cx="505" cy="435" r="3.5"/><circle cx="510" cy="430" r="3.5"/><circle cx="515" cy="437" r="3.5"/><circle cx="520" cy="430" r="3.5"/><circle cx="525" cy="423" r="3.5"/><circle cx="532" cy="397" r="3.5"/><circle cx="540" cy="403" r="3.5"/><circle cx="545" cy="385" r="3.5"/><circle cx="550" cy="388" r="3.5"/><circle cx="555" cy="380" r="3.5"/><circle cx="560" cy="350" r="3.5"/><circle cx="565" cy="345" r="3.5"/><circle cx="568" cy="335" r="3.5"/><circle cx="572" cy="340" r="3.5"/><circle cx="578" cy="265" r="3.5"/><circle cx="585" cy="263" r="3.5"/><circle cx="592" cy="263" r="3.5"/><circle cx="600" cy="268" r="3.5"/><circle cx="608" cy="285" r="3.5"/>
        <circle cx="612" cy="437" r="3.5"/><circle cx="615" cy="440" r="3.5"/><circle cx="625" cy="435" r="3.5"/><circle cx="630" cy="440" r="3.5"/><circle cx="640" cy="425" r="3.5"/><circle cx="645" cy="432" r="3.5"/><circle cx="650" cy="420" r="3.5"/><circle cx="655" cy="428" r="3.5"/><circle cx="660" cy="422" r="3.5"/><circle cx="665" cy="435" r="3.5"/><circle cx="670" cy="440" r="3.5"/><circle cx="675" cy="428" r="3.5"/><circle cx="678" cy="408" r="3.5"/><circle cx="682" cy="400" r="3.5"/><circle cx="688" cy="398" r="3.5"/><circle cx="690" cy="325" r="3.5"/><circle cx="692" cy="398" r="3.5"/><circle cx="695" cy="365" r="3.5"/><circle cx="698" cy="378" r="3.5"/><circle cx="704" cy="325" r="3.5"/><circle cx="708" cy="285" r="3.5"/><circle cx="710" cy="295" r="3.5"/><circle cx="722" cy="285" r="3.5"/><circle cx="726" cy="338" r="3.5"/><circle cx="730" cy="405" r="3.5"/><circle cx="735" cy="410" r="3.5"/><circle cx="738" cy="420" r="3.5"/><circle cx="740" cy="285" r="3.5"/><circle cx="745" cy="297" r="3.5"/><circle cx="742" cy="320" r="3.5"/><circle cx="752" cy="320" r="3.5"/><circle cx="756" cy="362" r="3.5"/><circle cx="758" cy="273" r="3.5"/><circle cx="765" cy="290" r="3.5"/><circle cx="768" cy="283" r="3.5"/><circle cx="772" cy="265" r="3.5"/><circle cx="778" cy="280" r="3.5"/><circle cx="785" cy="267" r="3.5"/><circle cx="790" cy="273" r="3.5"/><circle cx="792" cy="278" r="3.5"/>
      </g>
      <g fill="var(--blue)">
        <circle cx="238" cy="328" r="3.5"/><circle cx="240" cy="275" r="3.5"/><circle cx="244" cy="268" r="3.5"/><circle cx="250" cy="270" r="3.5"/><circle cx="255" cy="275" r="3.5"/><circle cx="258" cy="344" r="3.5"/><circle cx="262" cy="378" r="3.5"/><circle cx="268" cy="372" r="3.5"/><circle cx="270" cy="390" r="3.5"/><circle cx="275" cy="395" r="3.5"/><circle cx="272" cy="407" r="3.5"/><circle cx="280" cy="383" r="3.5"/><circle cx="286" cy="380" r="3.5"/><circle cx="290" cy="340" r="3.5"/><circle cx="293" cy="364" r="3.5"/><circle cx="287" cy="398" r="3.5"/><circle cx="300" cy="366" r="3.5"/><circle cx="304" cy="342" r="3.5"/><circle cx="306" cy="366" r="3.5"/><circle cx="310" cy="405" r="3.5"/><circle cx="318" cy="397" r="3.5"/><circle cx="322" cy="380" r="3.5"/><circle cx="330" cy="375" r="3.5"/><circle cx="335" cy="398" r="3.5"/><circle cx="338" cy="393" r="3.5"/><circle cx="342" cy="405" r="3.5"/><circle cx="348" cy="395" r="3.5"/><circle cx="351" cy="404" r="3.5"/><circle cx="356" cy="400" r="3.5"/><circle cx="366" cy="408" r="3.5"/><circle cx="370" cy="412" r="3.5"/><circle cx="372" cy="430" r="3.5"/><circle cx="378" cy="432" r="3.5"/><circle cx="385" cy="425" r="3.5"/><circle cx="390" cy="420" r="3.5"/><circle cx="393" cy="428" r="3.5"/><circle cx="398" cy="430" r="3.5"/><circle cx="402" cy="422" r="3.5"/><circle cx="405" cy="433" r="3.5"/><circle cx="412" cy="426" r="3.5"/><circle cx="418" cy="405" r="3.5"/><circle cx="422" cy="398" r="3.5"/><circle cx="428" cy="390" r="3.5"/><circle cx="432" cy="395" r="3.5"/><circle cx="436" cy="410" r="3.5"/><circle cx="440" cy="402" r="3.5"/><circle cx="446" cy="410" r="3.5"/><circle cx="452" cy="393" r="3.5"/><circle cx="455" cy="412" r="3.5"/><circle cx="460" cy="412" r="3.5"/><circle cx="465" cy="400" r="3.5"/><circle cx="470" cy="447" r="3.5"/><circle cx="475" cy="443" r="3.5"/><circle cx="480" cy="430" r="3.5"/><circle cx="485" cy="415" r="3.5"/><circle cx="490" cy="428" r="3.5"/><circle cx="495" cy="393" r="3.5"/><circle cx="500" cy="320" r="3.5"/><circle cx="502" cy="293" r="3.5"/><circle cx="507" cy="287" r="3.5"/><circle cx="511" cy="300" r="3.5"/><circle cx="514" cy="276" r="3.5"/><circle cx="518" cy="287" r="3.5"/><circle cx="526" cy="298" r="3.5"/><circle cx="530" cy="425" r="3.5"/><circle cx="535" cy="430" r="3.5"/><circle cx="540" cy="415" r="3.5"/><circle cx="545" cy="402" r="3.5"/><circle cx="550" cy="410" r="3.5"/><circle cx="560" cy="413" r="3.5"/><circle cx="565" cy="378" r="3.5"/><circle cx="570" cy="368" r="3.5"/><circle cx="575" cy="370" r="3.5"/><circle cx="578" cy="285" r="3.5"/><circle cx="582" cy="280" r="3.5"/><circle cx="588" cy="266" r="3.5"/><circle cx="595" cy="268" r="3.5"/><circle cx="601" cy="273" r="3.5"/><circle cx="606" cy="270" r="3.5"/><circle cx="612" cy="264" r="3.5"/>
      </g>
      <g fill="#4a9a2e"><circle cx="1035" cy="447" r="3.5"/><circle cx="1040" cy="447" r="3.5"/><circle cx="1045" cy="447" r="3.5"/></g>
      <g>
        <circle cx="1150" cy="262" r="3.5" fill="#8fb3dc"/><circle cx="1150" cy="280" r="3.5" fill="#f3b37a"/><circle cx="1150" cy="299" r="3.5" fill="#4a9a2e"/><circle cx="1150" cy="317" r="3.5" fill="#e48b8b"/><circle cx="1150" cy="336" r="3.5" fill="#c2a8de"/><circle cx="1150" cy="355" r="3.5" fill="#c4a39a"/><circle cx="1150" cy="373" r="3.5" fill="#f0b8e0"/><circle cx="1150" cy="392" r="3.5" fill="#c8c8c8"/><circle cx="1150" cy="410" r="3.5" fill="var(--olive)"/><circle cx="1150" cy="429" r="3.5" fill="#8fd8e6"/><circle cx="1150" cy="448" r="3.5" fill="var(--blue)"/>
        <text x="1167" y="265" font-family="Georgia, serif" fill="#333">Names</text>
      </g>
    </svg>
  </section>

  <div class="side-tab"><span>SELECT A MODEL</span></div>
  <svg class="side-toggle" width="30" height="30" viewBox="0 0 30 30"><circle cx="15" cy="15" r="13" fill="var(--navy)" stroke="#fff" stroke-width="2"/><circle cx="15" cy="15" r="8" fill="none" stroke="#fff" stroke-width="1.6"/><path d="M19 15h-8m3-3-3 3 3 3" fill="none" stroke="#fff" stroke-width="1.6"/></svg>

  <div class="export" style="left:400px">
    <svg width="26" height="22" viewBox="0 0 26 22" fill="none" stroke="var(--navy)" stroke-width="2.2"><path d="M12 4H3v16h17v-7"/><path d="M9 15c1-6 6-9 12-9M17 2l5 4-4 4"/></svg>Export</div>
  <div class="export" style="left:1160px">
    <svg width="26" height="22" viewBox="0 0 26 22" fill="none" stroke="var(--navy)" stroke-width="2.2"><path d="M12 4H3v16h17v-7"/><path d="M9 15c1-6 6-9 12-9M17 2l5 4-4 4"/></svg>Export</div>

  <section class="table stats">
    <div class="head"><div style="width:400px;border:none">Stats</div></div>
    <div class="body">
      <div class="row"><div class="col180">Stat 1</div><div class="col180">0.5</div></div>
      <div class="row"><div class="col180">Stat 2</div><div class="col180">-3</div></div>
      <div class="row"><div class="col180">Stat 3</div><div class="col180">30%</div></div>
      <div class="row"><div class="col180">Stat 4</div><div class="col180">0.5</div></div>
      <div class="row"><div class="col180">Stat 5</div><div class="col180">-3</div></div>
      <div class="row"><div class="col180">Stat 6</div><div class="col180">30%</div></div>
      <div class="scroll"></div>
    </div>
  </section>

  <section class="table trades">
    <div class="head"><div class="col180">Open</div><div class="col180">Close</div><div class="col180">Size</div><div class="col180" style="border:none">Return</div></div>
    <div class="body">
      <div class="row"><div class="col180">2018-04-05</div><div class="col180">2018-04-07</div><div class="col180">13</div><div class="col180">5%</div></div>
      <div class="row"><div class="col180">2018-04-05</div><div class="col180">2018-04-07</div><div class="col180">12</div><div class="col180">7%</div></div>
      <div class="row"><div class="col180">2018-04-05</div><div class="col180">2018-04-07</div><div class="col180">15</div><div class="col180">6%</div></div>
      <div class="row"><div class="col180">2018-04-05</div><div class="col180">2018-04-07</div><div class="col180">16</div><div class="col180">9%</div></div>
      <div class="row"><div class="col180">2018-04-05</div><div class="col180">2018-04-07</div><div class="col180">12</div><div class="col180">8%</div></div>
      <div class="row"><div class="col180">2018-04-05</div><div class="col180">2018-04-07</div><div class="col180">19</div><div class="col180">6%</div></div>
      <div class="scroll"></div>
    </div>
  </section>
</div>
</div>
</body>
</html>
```